Stonebrace Business Card Design

The Stonebrace Co is an aggregate (crushing) equipment dealer serving Western Canadian provinces. Stonebrace is a distributor of aggregate equipment for different manufacturers.

We are looking to change and update the existing business card which has been used since the existence of the company. A copy of existing card has been attached for reference. The Stonebrace Co logo we want to remain the same and we want the green color to remain the same.

We are wanting something new with a different look. A refreshing card to show a new modern and updated look. No longer wanting to have the manufacturers on the back of the card but something more like our logo on the back of the card with a statement like "Crushing Solutions"

ideas could be:
- card can be different colors on front and back
- front or reverse of the card could possibly be the green color with the logo in black

Target Market(s)

Owners of Aggregate/Crushing companies

Contact Information for Business Card

see above

Requirements
Must have
• - logo to remain same along with same font within logo
• - green color to remain same
Nice to have
• as noted above under project description
Should not have

```html
<!DOCTYPE html>
<html lang="en">
<head>
<meta charset="utf-8">
<title>Stonebrace Co – Business Card</title>
<link href="https://fonts.googleapis.com/css2?family=Roboto:wght@400;500;700&family=Roboto+Condensed:wght@700&display=swap" rel="stylesheet">
<style>
  :root {
    --backdrop: #5a4939;
    --card-white: #f4f4f2;
    --brand-green: #8b8c06;
    --ink: #231f20;
    --text-grey: #505050;
  }
  html, body {
    margin: 0;
    width: 1200px;
    height: 960px;
    overflow: hidden;
    background: var(--backdrop);
    font-family: "Roboto", Arial, sans-serif;
  }
  .card {
    position: absolute;
    width: 600px;
    height: 343px;
    border-radius: 18px;
    box-sizing: border-box;
  }
  .card-front { left: 314px; top: 113px; background: var(--card-white); }
  .card-back  { left: 311px; top: 472px; background: var(--brand-green); }

  .person { position: absolute; right: 42px; top: 38px; text-align: right; }
  .person-name {
    font-family: "Roboto Condensed", "Arial Narrow", sans-serif;
    font-weight: 700; font-size: 21px; color: var(--brand-green);
    margin: 0; line-height: 1.2; text-transform: uppercase;
  }
  .person-title { font-size: 14px; font-weight: 500; color: var(--ink); margin: 2px 0 0; }

  .address {
    position: absolute; left: 34px; top: 171px;
    font-size: 14px; line-height: 18px; color: var(--text-grey); margin: 0; font-style: normal;
  }
  .contact-list {
    position: absolute; left: 34px; top: 217px;
    list-style: none; margin: 0; padding: 0;
    font-size: 14px; line-height: 19.4px; color: var(--text-grey);
  }
  .contact-list li { display: flex; align-items: center; }
  .contact-list svg { width: 14px; height: 14px; margin-right: 9px; fill: var(--brand-green); flex: none; }

  .brand-small {
    position: absolute; right: 44px; bottom: 44px;
    display: flex; align-items: center; gap: 10px;
  }
  .brand-small .mark { width: 22px; height: 22px; border-radius: 50%; background: var(--brand-green); }
  .brand-small .brand-name { font-size: 14px; font-weight: 700; color: var(--ink); letter-spacing: 0.2px; }

  .brand-large {
    position: absolute; left: 0; right: 0; top: 96px;
    display: flex; flex-direction: column; align-items: center;
  }
  .brand-large .mark { width: 84px; height: 84px; border-radius: 50%; background: var(--ink); }
  .brand-large .brand-name {
    margin-top: 36px; font-size: 25px; font-weight: 700; color: var(--ink); letter-spacing: 0.2px;
  }
  .tagline {
    position: absolute; left: 0; right: 0; top: 291px; margin: 0;
    text-align: center; font-size: 15px; font-weight: 700; color: var(--ink);
  }
</style>
</head>
<body>
  <section class="card card-front">
    <div class="person">
      <p class="person-name">Dale Morrow</p>
      <p class="person-title">CEO/FOUNDER</p>
    </div>

    <address class="address">2215- 48B Street<br>Millbrook, Alberta T4X 1B7</address>

    <ul class="contact-list">
      <li><svg viewBox="0 0 16 16" aria-hidden="true"><path d="M3.5 1l2.6 3-1.4 1.8c.9 2 2.5 3.6 4.5 4.5L11 8.9l3 2.6-1.3 2.8C7 14 2 9 1.7 3.3z"/></svg>555.301.4420</li>
      <li><svg viewBox="0 0 16 16" aria-hidden="true"><path d="M4.5 1h7v14h-7zM6 2.5v9h4v-9zM7.3 12.6h1.4v1.2H7.3z" fill-rule="evenodd"/></svg>555.614.2089</li>
      <li><svg viewBox="0 0 16 16" aria-hidden="true"><path d="M4 1h8v4H4zM1 6h14v6h-3v3H4v-3H1zM5 10v3.5h6V10z" fill-rule="evenodd"/></svg>555.738.1163</li>
      <li><svg viewBox="0 0 16 16" aria-hidden="true"><path d="M1 4h14v9H1zM1.5 4.5L8 9l6.5-4.5" /><path d="M2 5l6 4 6-4" fill="none" stroke="#f4f4f2" stroke-width="1.2"/></svg>dale@stonebr.com</li>
      <li><svg viewBox="0 0 16 16" aria-hidden="true"><circle cx="8" cy="8" r="7"/><path d="M5 3.5c1.5 1 1 2.5 2.5 3s.5 2 1.5 2.5 1 2.5 0 4M10 2.5c-.5 1.5 1 2 2.5 2" fill="none" stroke="#f4f4f2" stroke-width="1.2"/></svg>www.stonebrace.ca</li>
    </ul>

    <div class="brand-small">
      <span class="mark" aria-hidden="true"></span>
      <span class="brand-name">THE STONEBRACE CO.</span>
    </div>
  </section>

  <section class="card card-back">
    <div class="brand-large">
      <span class="mark" aria-hidden="true"></span>
      <span class="brand-name">THE STONEBRACE CO.</span>
    </div>
    <p class="tagline">Crushing Solutions</p>
  </section>
</body>
</html>
```